kelvaro stationary business card and letterhead

THIS PROJECT IS TO DESIGN A BUSINESS CARD DOUBLE SIDES .

Reason: I AM WAITING FOR TESINU SUBMISION

Industry/Entity Type

Business

Font styles to use
Other font styles liked:
• Chose your font

```html
<!DOCTYPE html>
<html lang="en">
<head>
<meta charset="utf-8">
<title>Kelvaro Stationery</title>
<link href="https://fonts.googleapis.com/css2?family=Open+Sans:wght@400;600&display=swap" rel="stylesheet">
<style>
  :root {
    --bg: #ececec;
    --paper: #ffffff;
    --ink: #2f2f2f;
    --ink-soft: #555555;
    --accent: #e5ac17;
    --rule: #333333;
    --shadow: rgba(0,0,0,0.12);
  }
  * { box-sizing: border-box; margin: 0; padding: 0; }
  html, body { width: 1200px; height: 1000px; overflow: hidden; }
  body {
    background: var(--bg);
    font-family: "Open Sans", Arial, sans-serif;
    color: var(--ink);
    position: relative;
  }
  .brand { display: flex; align-items: center; gap: 8px; }
  .brand-dot { width: 22px; height: 22px; border-radius: 50%; background: var(--accent); flex: none; }
  .brand-name { font-weight: 600; letter-spacing: 2px; color: var(--ink); font-size: 22px; }

  /* Letterhead */
  .letterhead {
    position: absolute; left: 90px; top: 104px; width: 560px; height: 792px;
    background: var(--paper); box-shadow: 0 4px 18px var(--shadow);
    padding: 60px 64px 0;
  }
  .letterhead .brand { justify-content: center; margin-bottom: 48px; }
  .letter-body { font-size: 9.5px; line-height: 1.7; color: var(--ink-soft); }
  .letter-body p { margin-bottom: 14px; }
  .salutation { margin-bottom: 10px !important; }
  .signature {
    width: 120px; height: 36px; margin: 18px 0 6px auto;
    background: linear-gradient(90deg, #f4f4f4, #e6e6e6);
    border-radius: 3px;
  }
  .closing { margin-top: 8px; }
  .letter-footer {
    position: absolute; left: 64px; right: 64px; bottom: 56px;
    border-top: 1px solid var(--rule); padding-top: 12px;
    text-align: center; font-size: 9px; color: var(--ink);
  }
  .footer-row { display: flex; justify-content: center; gap: 14px; margin-bottom: 5px; }
  .contact-item { display: inline-flex; align-items: center; gap: 4px; }
  .icon { width: 9px; height: 9px; fill: var(--accent); flex: none; }

  /* Business cards */
  .card {
    position: absolute; left: 720px; width: 400px; height: 229px;
    background: var(--paper); box-shadow: 0 4px 18px var(--shadow);
  }
  .card-front { top: 190px; display: flex; align-items: center; justify-content: center; }
  .card-front .brand-name { font-size: 26px; }
  .card-front .brand-dot { width: 26px; height: 26px; }
  .card-back { top: 520px; padding: 0 30px; display: flex; align-items: center; justify-content: space-between; }
  .card-back .brand-name { font-size: 17px; }
  .card-back .brand-dot { width: 18px; height: 18px; }
  .card-details { text-align: right; font-size: 8.5px; line-height: 1.6; }
  .holder-name { font-size: 15px; color: var(--ink); }
  .holder-role { color: var(--accent); font-size: 8.5px; margin-bottom: 6px; }
  .card-details .contact-item { justify-content: flex-end; display: flex; }
  .square { width: 6px; height: 6px; background: var(--accent); flex: none; }
</style>
</head>
<body>

<section class="letterhead">
  <div class="brand">
    <span class="brand-dot"></span>
    <span class="brand-name">KELVARO</span>
  </div>
  <div class="letter-body">
    <p class="salutation">Dear Client,</p>
    <p>Thank you for the time you spent with our team last week. We have reviewed your current menu, supply chain and kitchen workflow, and we see clear room to improve margins while keeping quality high across every site.</p>
    <p>Our proposal covers sourcing, product development and staff training over six months. Each stage has its own goals, budget and review date, so you can follow progress and adjust priorities at any point.</p>
    <p>Please read the attached plan and let us know a suitable time to meet. We look forward to working with you.</p>
    <div class="signature" role="img" aria-label="Handwritten signature of Mara Vellin"></div>
    <p class="closing">Best regards,</p>
  </div>
  <footer class="letter-footer">
    <div class="footer-row">
      <span class="contact-item">
        <svg class="icon" viewBox="0 0 10 10"><path d="M5 0a3.5 3.5 0 0 0-3.5 3.5C1.5 6 5 10 5 10s3.5-4 3.5-6.5A3.5 3.5 0 0 0 5 0zm0 5a1.5 1.5 0 1 1 0-3 1.5 1.5 0 0 1 0 3z"/></svg>
        48 Orchard Lane, Brightwell, 20415, Country
      </span>
    </div>
    <div class="footer-row">
      <span class="contact-item">
        <svg class="icon" viewBox="0 0 10 10"><path d="M2 0h2l1 2.5-1.3 1a6 6 0 0 0 2.8 2.8l1-1.3L10 6v2a2 2 0 0 1-2 2A8 8 0 0 1 0 2a2 2 0 0 1 2-2z"/></svg>
        555-0192-47
      </span>
      <span class="contact-item">
        <svg class="icon" viewBox="0 0 10 10"><rect x="0" y="3" width="10" height="6" rx="1"/><rect x="2" y="0" width="6" height="3"/></svg>
        555-0192-48
      </span>
      <span class="contact-item">
        <svg class="icon" viewBox="0 0 10 10"><path d="M0 2h10v6H0z M0 2l5 3.5L10 2" stroke="#fff" stroke-width="0.8"/></svg>
        hello@kelvaro-mail.com
      </span>
      <span class="contact-item">
        <svg class="icon" viewBox="0 0 10 10"><circle cx="5" cy="5" r="5"/></svg>
        www.kelvaro-consult.com
      </span>
    </div>
  </footer>
</section>

<section class="card card-front">
  <div class="brand">
    <span class="brand-dot"></span>
    <span class="brand-name">KELVARO</span>
  </div>
</section>

<section class="card card-back">
  <div class="brand">
    <span class="brand-dot"></span>
    <span class="brand-name">KELVARO</span>
  </div>
  <div class="card-details">
    <div class="holder-name">Mara Vellin</div>
    <div class="holder-role">Managing Director</div>
    <span class="contact-item">555-0192-47 <span class="square"></span></span>
    <span class="contact-item">555-0192-48 <span class="square"></span></span>
    <span class="contact-item">555-0192-49 <span class="square"></span></span>
    <span class="contact-item">hello@kelvaro-mail.com <span class="square"></span></span>
    <span class="contact-item">www.kelvaro-consult.com <span class="square"></span></span>
  </div>
</section>

</body>
</html>
```